Stylish new business card needed!

Hello everyone! I am in need of a new business card design for an alarm company here in Hurricane WV. I have all fonts, color codes and logos provided for you use! We are a young company and like the style of a clean sleek looking business card. Would like it double sided, one side holding the logo and the other with your design!
Target Market(s)
The people that are looking for the newest tech for home automation and security
Industry/Entity Type
Alarm services; Home automation
Contact Information for Business Card
Name of person; position (Sales; Installer); Phone Number (555.418.7260); Employee cell Number; Website (www.GuardedByVelk.example); Employee Email; Double sided
Look and feel
Each slider illustrates characteristics of the customer's brand and the style your logo design should communicate.

```html
<!DOCTYPE html>
<html lang="en">
<head>
<meta charset="utf-8">
<title>Guarded By Velk – Business Card</title>
<link rel="stylesheet" href="https://fonts.googleapis.com/css2?family=Arimo:wght@400;700&display=swap">
<style>
  :root {
    --stage: #3b3b3b;
    --card-white: #ffffff;
    --card-black: #161616;
    --brand-orange: #f68d4e;
    --brand-grey: #999999;
    --text-light: #f2f2f2;
  }
  * { box-sizing: border-box; margin: 0; padding: 0; }
  html, body {
    width: 1200px; height: 689px; overflow: hidden;
    background: var(--stage);
    font-family: "Arimo", Arial, sans-serif;
  }
  .stage {
    width: 1200px; height: 689px;
    display: flex; align-items: center; justify-content: center; gap: 40px;
  }
  .card {
    position: relative;
    width: 540px; height: 310px;
    border-radius: 18px;
    overflow: hidden;
    box-shadow: 0 14px 30px rgba(0,0,0,.35);
  }
  /* Front */
  .card--front {
    background: var(--card-white);
    display: flex; flex-direction: column; align-items: center; justify-content: center; gap: 14px;
  }
  .brand-name {
    font-weight: 700;
    color: var(--brand-orange);
    letter-spacing: 2px;
    text-transform: uppercase;
    line-height: 1;
    white-space: nowrap;
  }
  .card--front .brand-name { font-size: 46px; }
  .tagline {
    font-weight: 700;
    color: var(--brand-orange);
    text-transform: uppercase;
    letter-spacing: 1.5px;
    white-space: nowrap;
  }
  .card--front .tagline { font-size: 15px; }

  /* Back */
  .card--back { background: var(--card-black); }
  .back-brand {
    position: absolute; left: 22px; top: 100px; width: 236px;
    display: flex; flex-direction: column; align-items: center; gap: 10px;
  }
  .card--back .brand-name { font-size: 20px; letter-spacing: 1px; }
  .card--back .tagline { font-size: 7.5px; letter-spacing: 0.6px; }
  .divider {
    position: absolute; left: 272px; top: 40px;
    width: 1px; height: 150px; background: var(--brand-orange);
  }
  .contact {
    position: absolute; left: 292px; top: 36px;
    color: var(--text-light);
  }
  .contact__name { font-weight: 700; font-size: 22px; color: var(--brand-orange); }
  .contact__role { font-size: 13px; margin-top: 2px; }
  .contact__list { list-style: none; margin-top: 14px; }
  .contact__list li { display: flex; align-items: center; gap: 8px; font-size: 12.5px; line-height: 18px; white-space: nowrap; }
  .contact__list svg { width: 11px; height: 11px; fill: var(--brand-orange); flex: none; }
  .accent { color: var(--brand-orange); }
  .contact__address { font-size: 13px; line-height: 17px; margin-top: 14px; }
  .wave { position: absolute; left: 0; bottom: 0; width: 540px; height: 120px; }
</style>
</head>
<body>
<main class="stage">
  <section class="card card--front" aria-label="Card front">
    <p class="brand-name">Guarded By Velk</p>
    <p class="tagline">Automation and Security Services</p>
  </section>

  <section class="card card--back" aria-label="Card back">
    <div class="back-brand">
      <p class="brand-name">Guarded By Velk</p>
      <p class="tagline">Automation and Security Services</p>
    </div>
    <div class="divider"></div>
    <div class="contact">
      <p class="contact__name">Daniel Ortner</p>
      <p class="contact__role">Managing Director</p>
      <ul class="contact__list">
        <li><svg viewBox="0 0 24 24"><path d="M6.6 10.8a15 15 0 0 0 6.6 6.6l2.2-2.2a1 1 0 0 1 1-.25 11.4 11.4 0 0 0 3.6.57 1 1 0 0 1 1 1V20a1 1 0 0 1-1 1A17 17 0 0 1 3 4a1 1 0 0 1 1-1h3.5a1 1 0 0 1 1 1c0 1.25.2 2.45.57 3.6a1 1 0 0 1-.25 1z"/></svg><span>555.418.7260</span></li>
        <li><svg viewBox="0 0 24 24"><path d="M7 1h10a2 2 0 0 1 2 2v18a2 2 0 0 1-2 2H7a2 2 0 0 1-2-2V3a2 2 0 0 1 2-2zm0 3v14h10V4z"/></svg><span>555.418.7260</span></li>
        <li><svg viewBox="0 0 24 24"><path d="M2 5h20v14H2zm2 2v.5l8 5 8-5V7z"/></svg><span>sales.velk@mail.example</span></li>
        <li><svg viewBox="0 0 24 24"><circle cx="12" cy="12" r="10"/></svg><span>www.<span class="accent">GuardedByVelk</span>.example</span></li>
      </ul>
      <p class="contact__address">1280 Ridgeway Lane<br>Larkfield, ST 10482</p>
    </div>
    <svg class="wave" viewBox="0 0 540 120" preserveAspectRatio="none" aria-hidden="true">
      <path d="M0 96 C150 110 320 70 540 6 L540 16 C320 84 150 118 0 106 Z" fill="var(--brand-grey)"/>
      <path d="M0 110 C160 122 330 84 540 20 L540 120 L0 120 Z" fill="var(--brand-orange)"/>
    </svg>
  </section>
</main>
</body>
</html>
```